Calden L - Premium Business Cards

Background of Calden L
Calden Leafworks is a cigar mobile lounge where guests become family. A place of luxury, relaxation, and ambiance is the global popularity demand. Calden Leafworks strives to provide first-class service of quality and products. Our goal is to ensure that every guest is treated and serviced as a VIP.

Calden Leafworks was founded by Dennis Markow Jr in January 2020. After 15 years of cigar reviews and research Dennis decided it was time to launch his own cigar brand and boutique cigar company. With a wealth of knowledge and years of experience Calden Leafworks was born. With opulence for all cultures, Calden Leafworks offers hand rolled cigars with premium blend tobacco from sweet to bold imported from Costa Rica, Dominican Republic, and Nicaragua. Thank you for your business!

Objective:
Create a business card template to be used for all employees. Design should communicate premium and classy. And should use earth tone colors.

Design should include:
1. Client wants to incorporate the cigar leaf
2. Logo
3. Tagline: Respect the smoke
3. Content info:
Kevin Oldacre
Owner
555-017-4863
koldacre@caldenleaf.com
caldenleafworks.com

```html
<!DOCTYPE html>
<html lang="en">
<head>
<meta charset="utf-8">
<title>Calden Leafworks – Business Cards</title>
<link rel="stylesheet" href="https://fonts.googleapis.com/css2?family=Lato:wght@400;700&display=swap">
<style>
  :root {
    --backdrop: #241f1b;
    --card: #110d0a;
    --card-edge: #2a221c;
    --ink: #f1ebe2;
    --ink-soft: #d8cfc2;
    --rule: #7a6a58;
    --leaf: #8a6a48;
  }
  * { margin: 0; padding: 0; box-sizing: border-box; }
  html, body { width: 1200px; height: 900px; overflow: hidden; }
  body {
    background: radial-gradient(ellipse at 50% 45%, #2e2721 0%, var(--backdrop) 70%);
    font-family: "Lato", Arial, sans-serif;
    color: var(--ink);
    position: relative;
  }
  .card {
    position: absolute;
    width: 525px;
    height: 300px;
    background: var(--card);
    border-radius: 22px;
    box-shadow: 0 0 0 1px var(--card-edge), 0 18px 40px rgba(0,0,0,.55);
    overflow: hidden;
  }
  .card--front { left: 50px; top: 470px; }
  .card--back { left: 625px; top: 130px; }

  .wordmark {
    font-weight: 700;
    text-transform: uppercase;
    color: var(--ink);
    white-space: nowrap;
  }
  .rule-dot {
    position: absolute;
    height: 1px;
    background: var(--rule);
  }
  .rule-dot::before, .rule-dot::after {
    content: ""; position: absolute; top: -2px;
    width: 5px; height: 5px; border-radius: 50%; background: var(--rule);
  }
  .rule-dot::before { left: -2px; }
  .rule-dot::after { right: -2px; }

  .leaf-art {
    position: absolute;
    border-radius: 50%;
    background: radial-gradient(ellipse at center, rgba(138,106,72,.35) 0%, rgba(138,106,72,0) 70%);
  }

  /* front */
  .front-logo {
    position: absolute; left: 30px; top: 150px; width: 250px; text-align: center;
  }
  .front-logo .leaf-art { left: 55px; top: -34px; width: 140px; height: 34px; }
  .front-logo .wordmark { font-size: 20px; letter-spacing: .6px; }
  .front-logo .rule-dot { top: 40px; width: 190px; left: 30px; }
  .divider {
    position: absolute; left: 300px; top: 70px; width: 1px; height: 160px;
    background: var(--rule);
  }
  .contact { position: absolute; left: 325px; top: 72px; }
  .contact__name { font-size: 19px; font-weight: 700; letter-spacing: .5px; text-transform: uppercase; }
  .contact__role { font-size: 14px; color: var(--ink-soft); margin: 2px 0 16px 12px; }
  .contact__line {
    display: flex; align-items: center; gap: 7px;
    font-size: 14.5px; color: var(--ink-soft); margin-bottom: 5px;
  }
  .contact__line svg { width: 14px; height: 14px; flex: none; }

  /* back */
  .back-logo {
    position: absolute; left: 0; right: 0; top: 105px; text-align: center;
  }
  .back-logo .leaf-art { left: 172px; top: -44px; width: 180px; height: 42px; }
  .back-logo .wordmark { font-size: 34px; letter-spacing: 1.5px; }
  .back-logo .rule-dot { top: 62px; width: 280px; left: 122px; }
  .tagline {
    position: absolute; left: 0; right: 0; top: 200px; text-align: center;
    font-size: 17px; letter-spacing: .5px; text-transform: uppercase; color: var(--ink);
  }
</style>
</head>
<body>

<section class="card card--back" aria-label="Card back">
  <div class="back-logo">
    <span class="leaf-art" role="img" aria-label="Cigar leaf artwork"></span>
    <div class="wordmark">Calden Leafworks</div>
    <span class="rule-dot"></span>
  </div>
  <p class="tagline">Respect the Smoke</p>
</section>

<section class="card card--front" aria-label="Card front">
  <div class="front-logo">
    <span class="leaf-art" role="img" aria-label="Cigar leaf artwork"></span>
    <div class="wordmark">Calden Leafworks</div>
    <span class="rule-dot"></span>
  </div>
  <span class="divider"></span>
  <div class="contact">
    <p class="contact__name">Kevin Oldacre</p>
    <p class="contact__role">Owner</p>
    <p class="contact__line">
      <svg viewBox="0 0 16 16" aria-hidden="true"><path d="M4 1.5l2.2 3-1.3 1.6c.9 2 2.4 3.5 4.4 4.4l1.6-1.3 3 2.2-1.2 2.6C7.4 14 2 8.6 1.5 3.3z" fill="none" stroke="#f1ebe2" stroke-width="1.4" stroke-linejoin="round"/></svg>
      555-017-4863
    </p>
    <p class="contact__line">
      <svg viewBox="0 0 16 16" aria-hidden="true"><rect x="1" y="3" width="14" height="10" fill="#f1ebe2"/><path d="M1 3l7 6 7-6" fill="none" stroke="#110d0a" stroke-width="1.3"/></svg>
      koldacre@caldenleaf.com
    </p>
    <p class="contact__line">
      <svg viewBox="0 0 16 16" aria-hidden="true"><circle cx="8" cy="8" r="7" fill="#f1ebe2"/><g fill="none" stroke="#110d0a" stroke-width="1"><ellipse cx="8" cy="8" rx="3" ry="7"/><path d="M1 8h14M2.2 4.5h11.6M2.2 11.5h11.6"/></g></svg>
      caldenleafworks.com
    </p>
  </div>
</section>

</body>
</html>
```